Elegant, Playful ReDesign of Paperlynx Website in wordpress - Budget has been raised

Project Brief: Paperlynx Website Redesign in WordPress

Introduction: Paperlynx, a cutting-edge document creation solution, aims to revolutionize the tedious process of crafting contracts, offers, forms, and other documents. By saving customers valuable time, streamlining workflows, and minimizing human error, Paperlynx has become an essential tool. As a technology company with a diverse clientele, we're set to boost our online presence through a refreshed WordPress website. Beyond a modernized website, we aspire to establish a stronger brand identity, incorporating graphic elements seamlessly into our online presence.

Current Status: Currently hosted on WordPress, Paperlynx's existing website serves its purpose but is ready for a visual transformation. Our goal is to maintain a modern and attractive appearance while upholding our commitment to simplicity and efficiency. Notably, the website is currently only in Danish. The redesigned structure should include a language switch function to cater to future international customers.

Objectives:
• Modern Aesthetic: Redesign the website with a fresh and modern vibe, reflecting innovation in the document creation sphere.
• User-Friendly: Prioritize an intuitive design for seamless navigation, ensuring visitors easily understand our offerings and benefits.
• Informative Content: Strike a balance between attractiveness and informativeness, clearly communicating Paperlynx's value proposition and simplifying business processes.
• Graphic Elements: Integrate visually appealing graphics that enhance the site's aesthetics and contribute to our overall visual identity. These elements should be versatile for future use in social media, advertisements, and other branding materials.
• Brand Recognition: Maintain our current logo and color scheme while exploring creative ways to establish a distinctive brand identity. The website should be a cornerstone for a cohesive branding strategy.
• Media Integration: Include images or videos on the website to enhance engagement. Find suitable, free-to-use visuals.
• Responsiveness: Ensure the design is responsive and works seamlessly on all devices.
• Demo Booking Form: Improve the design of the form to book a demo.
• Multilingual Support: Enable language transformation; the website is currently in Danish but should cater to other countries.

Guidelines:
• Typography: Up to the designer's discretion.
• Images/Videos: Must be free to use without additional charges.
• WordPress Theme: Use any WordPress theme below $100.
• Logo Redesign: Not needed; stick to the referenced color palette, as our new logo uses these colors.
• Color Palette: Stick to the existing company colors for consistency:
RGB
• #000b3c
• #004c6c
• #319ac3
• Greytones and white are also allowed
• Creativity Encouraged: Embrace creativity within the color palette for the layout, visuals, and overall user experience.

Conclusion: The Paperlynx website redesign marks an exciting opportunity to enhance our online presence. Our goal is to achieve a balance between a modern, attractive design and a clear, informative representation of our innovative solutions. We envision the revamped website as the foundation for a compelling online brand presence, with versatile graphic elements resonating across various digital platforms.

Sections that the website must include: Space for customer logos, space for testimonials, Space and redesign for display of price structure and price comparison, sections for company details and other information.

Design should also include a redesign of the customer cases section.
Generally there should just be a redesign of all things that are on the website.

Link to current website: https://paperlynx.example/

Target Market(s)

+50 employees.

Industry/Entity Type

Document automation

Coding

Coded - Design and coding required

Number of Pages Required

5+ page

Colors
0054AA
0677BA
7BADD7
CADEEF
E8F1F8

Requirements
Must have
• The new webpage must have the same pages as the current one. Frontpage, Book demo, About us, Case stories and Pricing

```html
<!DOCTYPE html>
<html lang="en">
<head>
<meta charset="utf-8">
<title>Paperlynx – Error-free contracts and quotes</title>
<link href="https://fonts.googleapis.com/css2?family=Barlow+Semi+Condensed:wght@500;600;700&family=Montserrat:wght@400;500;600;700&display=swap" rel="stylesheet">
<style>
:root{
  --navy:#000b3c;
  --deep:#004c6c;
  --sky:#319ac3;
  --ink:#1d2a3a;
  --muted:#5b6675;
  --pale:#cadeef;
  --mist:#e8f1f8;
  --panel:#c9dfe8;
  --footer:#0c2c4c;
  --white:#ffffff;
  --line:#d9dfe6;
}
*{box-sizing:border-box;margin:0;padding:0}
html,body{width:1200px;height:5226px;overflow:hidden}
body{font-family:"Montserrat",sans-serif;color:var(--ink);background:var(--white);font-size:12px;line-height:1.5}
h1,h2,h3,.brand,.label{font-family:"Barlow Semi Condensed",sans-serif}
section,header,footer{position:relative;width:1200px;overflow:hidden}
.btn{display:inline-block;border:1.5px solid var(--deep);color:var(--deep);font-size:10px;font-weight:600;padding:5px 12px;letter-spacing:.04em}
.btn-solid{display:inline-block;background:var(--sky);color:var(--white);font-weight:600;font-size:13px;padding:9px 24px;letter-spacing:.04em}
.placeholder{display:block}

/* hero */
.hero{height:600px;background:var(--white)}
.hero-bg{position:absolute;inset:0}
.brand-row{position:absolute;left:70px;top:26px;display:flex;align-items:center;gap:10px}
.brand-square{width:30px;height:30px;background:var(--sky)}
.brand{font-size:28px;font-weight:700;color:var(--deep);letter-spacing:.02em;line-height:1}
.nav{position:absolute;right:56px;top:28px;display:flex;gap:6px;align-items:center;font-size:10px;color:var(--white)}
.nav span{padding:4px 8px}
.nav .active{background:var(--white);color:var(--deep);font-weight:600}
.nav .login{background:var(--sky);font-weight:600}
.hero-art{position:absolute;left:70px;top:160px}
.hero-copy{position:absolute;left:600px;top:150px;color:var(--white)}
.hero-copy h1{font-size:44px;font-weight:700;line-height:1.05;width:380px}
.hero-copy ul{list-style:none;margin-top:36px;font-size:15px;line-height:2}

/* features */
.features{height:180px;display:flex;justify-content:center;gap:60px;padding-top:40px}
.feature{width:240px;text-align:center}
.feature svg{margin:0 auto 6px}
.feature h3{font-family:"Montserrat",sans-serif;font-size:12px;font-weight:700;color:var(--navy)}
.feature p{font-size:9px;color:var(--muted);margin-top:2px}

/* clients */
.clients{height:310px;text-align:center}
.section-title{font-size:30px;font-weight:700;color:var(--deep);letter-spacing:.01em}
.clients .section-title{margin-top:10px}
.logo-grid{display:grid;grid-template-columns:repeat(5,180px);justify-content:center;row-gap:34px;margin-top:36px}
.client-name{font-family:"Montserrat",sans-serif;font-size:20px;font-weight:600;color:#3a3f47;display:flex;align-items:center;justify-content:center;gap:8px;height:40px}
.client-dot{width:12px;height:12px;background:#3a3f47;border-radius:50%}

/* testimonials */
.testimonials{height:560px;text-align:center}
.testimonials .section-title{margin-top:30px}
.quotes{position:relative;height:300px;margin-top:60px}
.quote{position:absolute;top:0;width:370px;background:#ececec;border-radius:6px;padding:44px 36px 24px;font-size:11px;color:#444;text-align:center;height:170px}
.quote.side{opacity:.45;width:300px}
.quote-mark{position:absolute;top:-18px;left:50%;transform:translateX(-50%);width:36px;height:36px;border-radius:50%;background:var(--deep)}
.quote-mark::after{content:"\201C";color:var(--white);font-size:30px;line-height:46px;font-family:Georgia,serif}
.quote.side .quote-mark{background:var(--sky)}
.author{position:absolute;top:190px;display:flex;gap:12px;text-align:left;align-items:center}
.avatar{width:60px;height:60px;border-radius:50%;background:linear-gradient(135deg,#8b7a6a,#c8b8a6)}
.author b{display:block;font-size:15px;color:var(--ink);font-weight:600}
.author small{font-size:11px;color:#888}
.dots{position:absolute;top:290px;left:50%;transform:translateX(-50%);display:flex;gap:14px}
.dots i{width:8px;height:8px;border-radius:50%;background:#bbb}
.dots i:first-child{background:#666}

/* intelligent solution */
.solution{height:680px}
.solution-inner{position:absolute;left:0;top:0;width:1200px;height:680px}
.solution h2{position:absolute;top:90px;width:100%;text-align:center;color:var(--white);font-size:32px;font-weight:700;line-height:1.05}
.solution .lead{position:absolute;top:190px;left:330px;width:540px;text-align:center;color:#dbe6ef;font-size:10px}
.steps{position:absolute;top:290px;left:110px;display:flex;gap:30px}
.step{width:300px;height:280px;position:relative}
.step .label{position:absolute;left:0;right:0;bottom:12px;text-align:center;color:var(--white);font-size:18px;font-weight:600}

/* sign */
.sign{height:800px;text-align:center}
.sign .section-title{margin-top:40px}
.sign .intro{width:680px;margin:16px auto 0;font-size:11px;color:var(--muted)}
.video{margin:24px auto 0}
.cards{display:flex;justify-content:center;gap:46px;margin-top:60px;text-align:left}
.card{width:380px;padding:26px 30px;border-radius:14px}
.card.tint{background:var(--pale)}
.card h3{font-family:"Montserrat",sans-serif;font-size:15px;font-weight:600;color:var(--deep);margin-bottom:12px}
.card p{font-size:10px;color:var(--muted);margin-bottom:10px}

/* crm */
.crm{height:920px;text-align:center}
.crm-bg{position:absolute;inset:0}
.crm .content{position:relative}
.crm .section-title{padding-top:50px;color:var(--navy)}
.partners{display:flex;justify-content:center;gap:40px;margin-top:10px;font-family:"Montserrat",sans-serif;font-size:26px;font-weight:600;color:var(--deep)}
.crm .intro{width:620px;margin:20px auto 0;font-size:11px;color:var(--muted)}
.crm .video{margin-top:26px}
.cols{display:flex;justify-content:center;gap:50px;margin-top:60px;text-align:left}
.col{width:260px}
.col h3{font-family:"Montserrat",sans-serif;font-size:15px;font-weight:600;color:var(--navy);margin-bottom:12px}
.col p{font-size:10px;color:var(--muted);margin-bottom:10px}

/* demo band */
.demo{height:290px;color:var(--white);text-align:center}
.demo h2{position:relative;padding-top:70px;font-size:34px;font-weight:700}
.demo p{position:relative;width:540px;margin:14px auto 0;font-size:11px;color:#d5e1ec}
.demo .btn-solid{position:relative;margin-top:26px}
.demo .play{position:absolute;left:250px;top:160px}

/* mobile */
.mobile{height:526px}
.mobile h2{position:absolute;left:198px;top:50px;font-size:32px;font-weight:700;color:var(--sky)}
.mobile .copy{position:absolute;left:198px;top:118px;width:380px;font-size:11px;color:var(--ink)}
.mobile .copy p{margin-bottom:16px}
.mobile .btn-solid{position:absolute;left:198px;top:395px;background:var(--deep);font-size:12px}
.mobile .art{position:absolute;left:600px;top:40px}

/* footer */
.footer{height:360px;background:var(--footer);color:var(--white)}
.footer .brand-box{position:absolute;left:185px;top:40px;background:var(--white);padding:14px 22px;display:flex;align-items:center;gap:10px}
.footer .brand{font-size:26px}
.f-col{position:absolute;top:120px;font-size:11px;line-height:1.75}
.f-col.links{font-size:10px;font-weight:600;letter-spacing:.04em;line-height:2}
.f-col h4{font-size:12px;font-weight:600}
.socials{display:flex;gap:8px;margin-top:6px}
.socials i{width:18px;height:18px;border-radius:50%;background:var(--white)}
.copyright{position:absolute;bottom:40px;width:100%;text-align:center;font-size:9px;color:#9fb2c4}
</style>
</head>
<body>

<header class="hero">
  <svg class="hero-bg" width="1200" height="600" viewBox="0 0 1200 600" role="img" aria-label="Office photo with paper files in deep blue tones">
    <defs>
      <linearGradient id="heroGrad" x1="0" y1="0" x2="1" y2="1">
        <stop offset="0" stop-color="#0a4e72"/>
        <stop offset="0.6" stop-color="#063a5a"/>
        <stop offset="1" stop-color="#002a48"/>
      </linearGradient>
    </defs>
    <path d="M560 0 H1200 V600 H440 C480 480 520 380 535 270 C548 170 552 80 560 0 Z" fill="url(#heroGrad)"/>
  </svg>
  <div class="brand-row">
    <span class="brand-square"></span>
    <div class="brand">PAPERLYNX</div>
  </div>
  <nav class="nav">
    <span class="active">Home</span><span>Customer Cases</span><span>Video</span><span>Live Demo</span><span>Prices</span><span>About Us</span><span class="login">Login</span><span>English ▾</span>
  </nav>
  <svg class="hero-art placeholder" width="520" height="330" role="img" aria-label="Illustration of laptop, tablet and phone showing the document flow, with a person working on a laptop">
    <rect width="520" height="330" rx="10" fill="#dbe7ef"/>
  </svg>
  <div class="hero-copy">
    <h1>Create Error-free Contracts and Quotes Quickly</h1>
    <ul>
      <li>· Get Paragraphs Inserted Automatically</li>
      <li>· Get Prices Calculated Automatically</li>
      <li>· Eliminate Manual Work</li>
      <li>·Sign Digitally</li>
    </ul>
  </div>
</header>

<section class="features">
  <div class="feature">
    <svg width="44" height="44" viewBox="0 0 44 44"><circle cx="22" cy="22" r="18" fill="none" stroke="#319ac3" stroke-width="3"/><path d="M22 12v10l7 5" fill="none" stroke="#319ac3" stroke-width="3" stroke-linecap="round"/></svg>
    <h3>SAVE TIME</h3>
    <p>Reduce your time consumption by up to 90% when creating customer contracts and offers.</p>
  </div>
  <div class="feature">
    <svg width="44" height="44" viewBox="0 0 44 44"><circle cx="22" cy="22" r="18" fill="none" stroke="#319ac3" stroke-width="3"/><path d="M14 22l6 6 11-12" fill="none" stroke="#319ac3" stroke-width="3" stroke-linecap="round"/></svg>
    <h3>HIGH QUALITY</h3>
    <p>Automation gives you minimal manual work and eliminates errors in your documents.</p>
  </div>
  <div class="feature">
    <svg width="44" height="44" viewBox="0 0 44 44"><rect x="4" y="6" width="14" height="10" rx="3" fill="none" stroke="#319ac3" stroke-width="3"/><rect x="26" y="17" width="14" height="10" rx="3" fill="none" stroke="#319ac3" stroke-width="3"/><rect x="4" y="28" width="14" height="10" rx="3" fill="none" stroke="#319ac3" stroke-width="3"/><path d="M18 11h4v22h-4M22 22h4" fill="none" stroke="#319ac3" stroke-width="2"/></svg>
    <h3>STREAMLINED FLOW</h3>
    <p>Be guided all the way through the document and ask for review before sending the document for digital signature.</p>
  </div>
</section>

<section class="clients">
  <h2 class="section-title">1000+ COMPANIES TRUST</h2>
  <div class="logo-grid">
    <div class="client-name">Brightpath</div>
    <div class="client-name"><span class="client-dot"></span>Lumen Law</div>
    <div class="client-name">Cartonix</div>
    <div class="client-name">Webshelf</div>
    <div class="client-name">Quillo Docs</div>
    <div class="client-name">Veltra</div>
    <div class="client-name">Norvik</div>
    <div class="client-name">CoreDesk</div>
    <div class="client-name">Kestrel Legal</div>
    <div class="client-name">Halvorsen</div>
  </div>
</section>

<section class="testimonials">
  <h2 class="section-title">Appreciated And Recommended By</h2>
  <div class="quotes">
    <div class="quote side" style="left:-60px">
      <span class="quote-mark"></span>
      <p>We had been looking for a long time for the right way to digitize our unique offers, and the tools we tried kept failing us.</p>
      <p style="margin-top:10px">It places high demands on the solution when complex offers need to be digitized, and we never had to compromise.</p>
    </div>
    <div class="quote" style="left:415px">
      <span class="quote-mark"></span>
      <p>I didn't imagine our offer could be fully automated just like that, but we gave it a shot because I saw what others had done with Paperlynx.</p>
      <p style="margin-top:10px">The result has become razor sharp – I am completely happy when I stand with a new offer in my hand.</p>
    </div>
    <div class="quote side" style="left:835px">
      <span class="quote-mark"></span>
      <p>We had been looking for a long time for the right tool to digitize our unique paragraph collection, and had no doubt after trying it.</p>
      <p style="margin-top:10px">It places high demands on the solution when complex paragraphs are to be digitized, and we got them all.</p>
    </div>
    <div class="author" style="left:-40px;opacity:.45"><div><b>Jonas Bak Olsen</b><small>Manager – Quillo Docs</small></div></div>
    <div class="author" style="left:415px"><span class="avatar" role="img" aria-label="Portrait photo of the reviewer"></span><div><b>Mads Holm Larsen</b><small>Sales director – Vaultline Security</small></div></div>
    <div class="author" style="left:840px;opacity:.6"><span class="avatar" role="img" aria-label="Portrait photo of the reviewer"></span><div><b>Jonas Bak Olsen</b><small>Manager – Quillo Docs</small></div></div>
    <div class="dots"><i></i><i></i><i></i><i></i></div>
  </div>
</section>

<section class="solution">
  <svg class="solution-inner" width="1200" height="680" viewBox="0 0 1200 680" role="img" aria-label="Dark blue photo of a person typing on a laptop">
    <defs>
      <linearGradient id="solGrad" x1="0" y1="0" x2="1" y2="1">
        <stop offset="0" stop-color="#1e2f4a"/>
        <stop offset="0.6" stop-color="#16304e"/>
        <stop offset="1" stop-color="#0d3a5a"/>
      </linearGradient>
    </defs>
    <path d="M0 0 H880 C1060 0 1200 140 1200 320 V680 H0 Z" fill="url(#solGrad)"/>
  </svg>
  <h2>Intelligent Document<br>Solution</h2>
  <p class="lead">Leave the creation of your documents to our intelligent solution. It can automatically calculate your prices and insert the sections that need to be included in your documents. Get rid of manual work with legal uncertainties and become more efficient.<br><br>Choose one of your automated documents, fill in the question frame and sign digitally – it's that simple!</p>
  <div class="steps">
    <div class="step">
      <svg width="300" height="280" role="img" aria-label="Screenshot of the document selection list"><rect width="300" height="280" fill="#6d7480"/><rect x="10" y="10" width="280" height="210" fill="#8a929c"/></svg>
      <span class="label">1. Select document</span>
    </div>
    <div class="step">
      <svg width="300" height="280" role="img" aria-label="Screenshot of the guided question form"><rect width="300" height="280" fill="#2c3e55"/><rect x="10" y="10" width="280" height="210" fill="#ffffff"/></svg>
      <span class="label">2. Complete guided flow</span>
    </div>
    <div class="step">
      <svg width="300" height="280" role="img" aria-label="Screenshot of the signing view on a document"><rect width="300" height="280" fill="#2c3e55"/><rect x="10" y="10" width="280" height="210" fill="#ffffff"/></svg>
      <span class="label">3. Sign digitally</span>
    </div>
  </div>
</section>

<section class="sign">
  <h2 class="section-title">Sign With SIGNARA</h2>
  <p class="intro">Send your documents for signature with one of the Nordics' leading and most secure digital signature solutions. Signara has, for example, been accepted on the EU's trusted list, which only Trustgate and the national registry have achieved in Denmark.</p>
  <svg class="video" width="420" height="230" role="img" aria-label="Video showing the digital signature overview in the signing dashboard">
    <rect width="420" height="230" fill="#1a1f2a"/>
    <rect x="8" y="30" width="404" height="165" fill="#f4f6f8"/>
    <text x="30" y="18" fill="#ffffff" font-family="Montserrat, sans-serif" font-size="12">Digital Signatures &amp; Digital Documents</text>
    <rect x="8" y="200" width="404" height="3" fill="#555"/><rect x="8" y="200" width="250" height="3" fill="#e03030"/>
    <text x="330" y="220" fill="#ffffff" font-family="Montserrat, sans-serif" font-size="10">Video</text>
  </svg>
  <div class="cards">
    <div class="card tint">
      <h3>Digital signature</h3>
      <p>Send your automated documents for digital signature or upload your own with a few clicks – quickly and easily.</p>
      <p>The solution automatically sends reminders about signatures, and you can keep an eye on how far the signer is in the signature process along the way.</p>
      <p>Get your offers signed more often and faster with a digital signature for the benefit of both yourself and the signatories.</p>
      <span class="btn">READ MORE</span>
    </div>
    <div class="card">
      <h3>Mass broadcast</h3>
      <p>Send the same document for signature by many different signers at once or personalize the document with merged information.</p>
      <p>You can also ask the user for input before a document is created and signed.</p>
      <p>Start your mass broadcast and wait for the solution to automatically collect signatures from hundreds or thousands of users.</p>
      <span class="btn">READ MORE</span>
    </div>
  </div>
</section>

<section class="crm">
  <svg class="crm-bg" width="1200" height="920" viewBox="0 0 1200 920" aria-hidden="true">
    <path d="M0 120 C0 40 60 0 140 0 H1060 C1140 0 1200 40 1200 120 V580 C1200 740 1100 800 1000 800 H0 Z" fill="#c9dfe8"/>
  </svg>
  <div class="content">
    <h2 class="section-title">Integration To CRM</h2>
    <div class="partners"><span>CoreDesk</span><span>Webshelf</span></div>
    <p class="intro">Create your offers or customer contracts directly in your CRM solution, and send them for digital signature with a few clicks. Experience better insight and timing in your sales with an integration to CoreDesk. The integration has been created in collaboration with Webshelf.</p>
    <svg class="video" width="440" height="260" role="img" aria-label="Video walkthrough of the CRM integration">
      <rect width="440" height="260" fill="#ffffff"/>
      <rect x="8" y="8" width="424" height="244" fill="#1a1f2a"/>
      <rect x="16" y="36" width="408" height="180" fill="#eef1f4"/>
      <text x="30" y="26" fill="#ffffff" font-family="Montserrat, sans-serif" font-size="12">Paperlynx Module for CoreDesk walkthrough</text>
      <rect x="16" y="226" width="408" height="3" fill="#555"/>
      <text x="355" y="245" fill="#ffffff" font-family="Montserrat, sans-serif" font-size="10">Video</text>
    </svg>
    <div class="cols">
      <div class="col">
        <h3>Digital signature</h3>
        <p>Send your automated documents for digital signature or upload your digital signature. Send your offers for digital signature with data directly from your CRM solution – quickly and easily.</p>
        <p>Keep an eye on how far the customer is in the process, the signature process and get the status updated in CRM the solution along the way.</p>
        <p>Get your offers signed more often and faster with a digital signature.</p>
        <span class="btn">READ MORE</span>
      </div>
      <div class="col">
        <h3>Automated offers</h3>
        <p>Create error-free offers with data from your CRM solution using a guided flow and avoid manual errors.</p>
        <p>Get tailored your offers down to the smallest detail and get sections all relevant sections and calculate your prices automatically.</p>
        <p>Send the offer for digital signature and get the status updated along the way in the CRM solution.</p>
        <span class="btn">READ MORE</span>
      </div>
      <div class="col">
        <h3>Leads from your Website</h3>
        <p>Manage your leads and customer inquiries with intelligent forms directly on your own website.</p>
        <p>Give your lead an estimate price or offer draft immediately, which you can work on from your CRM solution.</p>
        <p>Get created leads automatically in your CRM solution for easy follow-up.</p>
        <span class="btn">READ MORE</span>
      </div>
    </div>
  </div>
</section>

<section class="demo">
  <svg style="position:absolute;inset:0" width="1200" height="290" role="img" aria-label="Dark photo of hands typing on a laptop">
    <defs><linearGradient id="demoGrad" x1="0" y1="0" x2="1" y2="0"><stop offset="0" stop-color="#1d2b3e"/><stop offset="0.5" stop-color="#15314d"/><stop offset="1" stop-color="#0e2a47"/></linearGradient></defs>
    <rect width="1200" height="290" fill="url(#demoGrad)"/>
  </svg>
  <svg class="play" width="50" height="50" viewBox="0 0 50 50" aria-hidden="true"><circle cx="25" cy="25" r="23" fill="none" stroke="#ffffff" stroke-width="2" opacity=".6"/><path d="M20 15l14 10-14 10z" fill="#ffffff" opacity=".6"/></svg>
  <h2>START LIVE DEMO</h2>
  <p>Experience the intuitive and intelligent flow for creating documents on your own. In a few minutes you have a complete document – ready for digital signature.</p>
  <span class="btn-solid">START LIVE DEMO</span>
</section>

<section class="mobile">
  <h2>Activate Your Mobile</h2>
  <div class="copy">
    <p>Create your documents when it suits you. They can be created on any device and signed much faster.</p>
    <p>Select document<br>Complete the question frame<br>Sign digitally</p>
    <p>For example, create an offer on a mobile or a tablet while talking to a potential customer at a meeting. Get approval instantly and send it for digital signature before you go home.</p>
  </div>
  <span class="btn-solid">GET STARTED</span>
  <svg class="art" width="420" height="420" viewBox="0 0 420 420" role="img" aria-label="Illustration of a phone and tablet showing the document creation flow">
    <rect x="-30" y="170" width="470" height="190" fill="#c9dfe8"/>
    <rect x="180" y="0" width="230" height="330" rx="16" fill="#1b1f26"/>
    <rect x="190" y="14" width="210" height="300" rx="6" fill="#e8f1f8"/>
    <rect x="50" y="90" width="130" height="250" rx="14" fill="#1b1f26"/>
    <rect x="58" y="104" width="114" height="222" rx="6" fill="#e8f1f8"/>
  </svg>
</section>

<footer class="footer">
  <div class="brand-box"><span class="brand-square"></span><div class="brand">PAPERLYNX</div></div>
  <div class="f-col" style="left:185px">
    Mail: contact@paperlynx.example<br>
    Phone: +45 12 34 56 78<br>
    Address: Lindevej 12, 2600 Glostrup<br>
    Follow us on
    <div class="socials"><i></i><i></i><i></i><i></i></div>
  </div>
  <div class="f-col links" style="left:510px">HOME<br>CUSTOMER REVIEW<br>VIDEO DEMO<br>PRICES<br>ABOUT US</div>
  <div class="f-col" style="left:740px">
    <h4>Meet Us Online</h4>
    We Would Love To Link And Share<br>Thoughts And Ideas. Follow Us And Stay<br>Updated On The Latest News.
  </div>
  <div class="copyright">Copyright © 2024 Paperlynx. All rights reserved.</div>
</footer>

</body>
</html>
```